I need a website, primarily a landing page, for my company, Morrow Vantage. A sales training and cons

I need a web design/landing page for a new sales training and consulting company, morrow vantage. We perform "sales experiments" aimed at each individual or team, where we assist in helping them identify their strengths, through a series of "sales experiments" that we can tailor based on the individual and what they're trying to accomplish.

```html
<!DOCTYPE html>
<html lang="en">
<head>
<meta charset="utf-8">
<title>Morrow Vantage — Sales Training &amp; Consulting</title>
<link rel="stylesheet" href="https://fonts.googleapis.com/css2?family=Open+Sans:wght@300;400;600&family=Poppins:wght@500;600&display=swap">
<style>
  :root {
    --brand-blue: #2f77b5;
    --hero-dark: #0d0d0e;
    --hero-mid: #1a1b1d;
    --panel-dark: #222326;
    --white: #ffffff;
    --ink: #141414;
    --body-grey: #6b6b6b;
  }
  * { box-sizing: border-box; margin: 0; padding: 0; }
  html, body { width: 1114px; height: 1200px; overflow: hidden; background: var(--white); }
  body { position: relative; font-family: "Open Sans", Arial, sans-serif; }

  .hero {
    position: absolute; left: 39px; top: 58px; width: 1034px; height: 519px;
    background: radial-gradient(ellipse at 50% 45%, var(--hero-mid) 0%, var(--hero-dark) 70%);
  }
  .hero-curve { position: absolute; left: 39px; top: 576px; width: 1034px; height: 26px; display: block; }

  .site-nav a {
    position: absolute; top: 28px; color: var(--white); text-decoration: none;
    font-size: 13.5px; line-height: 16px;
  }
  .site-nav a.is-active { color: var(--brand-blue); }
  .nav-home { left: 60px; } .nav-about-brand { left: 142px; } .nav-about-me { left: 315px; }
  .nav-experiments { left: 727px; } .nav-blog { left: 851px; } .nav-contact { left: 922px; }

  .brand-panel {
    position: absolute; left: 386px; top: 0; width: 271px; height: 106px;
    background: var(--panel-dark);
    display: flex; align-items: center; justify-content: center;
  }
  .brand-name { font-family: "Poppins", Arial, sans-serif; font-weight: 500; font-size: 20px; color: var(--white); }

  .hero-copy { position: absolute; left: 0; top: 190px; width: 100%; text-align: center; color: var(--white); }
  .hero-tagline { font-weight: 300; font-size: 24px; line-height: 32px; }
  .hero-title { font-family: "Poppins", Arial, sans-serif; font-weight: 600; font-size: 46px; line-height: 60px; margin-top: 8px; }
  .hero-title .accent { color: var(--brand-blue); }
  .hero-lead { font-size: 13.5px; margin-top: 6px; }
  .hero-actions { display: flex; justify-content: center; gap: 16px; margin-top: 18px; }
  .btn {
    display: inline-flex; align-items: center; justify-content: center; height: 34px;
    border-radius: 17px; font-size: 13.5px; color: var(--white); text-decoration: none;
  }
  .btn-primary { width: 160px; background: var(--brand-blue); }
  .btn-outline { width: 142px; border: 1.5px solid var(--white); }

  .about-head { position: absolute; left: 0; top: 710px; width: 1114px; text-align: center; }
  .about-title { font-family: "Poppins", Arial, sans-serif; font-weight: 600; font-size: 32px; line-height: 42px; color: var(--ink); }
  .about-title .accent { color: var(--brand-blue); }
  .about-rule { display: block; width: 78px; height: 2px; background: var(--brand-blue); margin: 2px auto 0; }
  .about-sub { font-size: 14px; color: var(--body-grey); margin-top: 4px; }

  .about-text {
    position: absolute; left: 94px; top: 830px; width: 432px;
    font-size: 14.2px; line-height: 21px; color: var(--body-grey);
  }
  .about-visual {
    position: absolute; left: 573px; top: 834px; width: 445px; height: 242px;
    background: radial-gradient(ellipse at 50% 50%, #2a2b2e 0%, #121214 75%);
  }
</style>
</head>
<body>
  <header class="hero">
    <nav class="site-nav">
      <a class="nav-home is-active" href="#">Home</a>
      <a class="nav-about-brand" href="#">About Morrow Vantage</a>
      <a class="nav-about-me" href="#">About me</a>
      <a class="nav-experiments" href="#">Experiments</a>
      <a class="nav-blog" href="#">Blog</a>
      <a class="nav-contact" href="#">Contact</a>
    </nav>
    <div class="brand-panel"><span class="brand-name">Morrow Vantage</span></div>
    <div class="hero-copy">
      <p class="hero-tagline">Success. It's in your DNA</p>
      <h1 class="hero-title">Morrow<span class="accent">Vantage</span></h1>
      <p class="hero-lead">Will Help You To Find</p>
      <div class="hero-actions">
        <a class="btn btn-primary" href="#">Know About Us</a>
        <a class="btn btn-outline" href="#">Get in Touch</a>
      </div>
    </div>
  </header>
  <svg class="hero-curve" viewBox="0 0 1034 26" preserveAspectRatio="none" aria-hidden="true">
    <path d="M0 0 H1034 Q517 52 0 0 Z" fill="#0d0d0e"/>
  </svg>

  <section class="about-head">
    <h2 class="about-title">About <span class="accent">Morrow Vantage</span></h2>
    <span class="about-rule"></span>
    <p class="about-sub">Lorem ipsum dolor sit amet, consectetur adipiscing elit.</p>
  </section>

  <p class="about-text">Lorem ipsum dolor sit amet, consectetur adipiscing elit, sed do eiusmod tempor incididunt ut labore et dolore magna aliqua. Ut enim ad minim veniam, quis nostrud exercitation ullamco laboris nisi ut aliquip ex ea commodo consequat. Lorem ipsum dolor sit amet, consectetur adipiscing elit, sed do eiusmod tempor incididunt ut labore et dolore magna aliqua. Ut enim ad minim veniam, quis nostrud exercitation ullamco laboris nisi ut aliquip ex ea commodo consequat. Lorem ipsum dolor sit amet, consectetur adipiscing elit, sed do eiusmod tempor incididunt ut labore et dolore magna aliqua. Ut enim ad minim veniam, quis nostrud exercitation ullamco laboris nisi ut aliquip ex ea commodo consequat.</p>

  <div class="about-visual" role="img" aria-label="Morrow Vantage brand image on a dark textured background"></div>
</body>
</html>
```